Verodex business card

Business card for sustainable investment company called "Verodex". Verodex is an exchange platform selling carbon credits between buyers and sellers. Carbon Credits are an environmental commodity for reducing global carbon emissions.

the card should obviously have our logo and the theme should be sustainability/environment mixed with a trading platform.

Contact Information for Business Card

Logo, Name, Title, Phone, Email

Colors
0054AA
0677BA
7BADD7
CADEEF
E8F1F8
0094D4
00A9DD
6FCCEA
C7EBF8
E9F6FB
00AB8E
00BBA5
67D7C9
C6EFE9
E9F9F6
59FF00
82FF00
B8FF75
E3FFCB
F4FFEA

```html
<!DOCTYPE html>
<html lang="en">
<head>
<meta charset="UTF-8">
<title>Verodex Business Card</title>
<link href="https://fonts.googleapis.com/css2?family=Poppins:wght@400;500;600&display=swap" rel="stylesheet">
<style>
  :root {
    --navy: #22334d;
    --white: #ffffff;
    --cyan: #35e6ee;
    --blue: #2176ec;
    --brand: #2a9cef;
    --backdrop: #a6a6a6;
    --ink: #1d2433;
  }
  * { margin: 0; padding: 0; box-sizing: border-box; }
  html, body {
    width: 1093px; height: 1200px; overflow: hidden;
    background: var(--backdrop);
    font-family: 'Poppins', sans-serif;
  }
  .canvas { position: relative; width: 1093px; height: 1200px; }

  .card {
    position: absolute; left: 264px;
    border-radius: 36px; overflow: hidden;
    background: var(--white);
  }

  /* Front */
  .card-front { top: 226px; width: 582px; height: 357px; }
  .front-band {
    position: absolute; left: 0; top: 0; width: 100%; height: 290px;
    background: var(--navy);
  }
  .front-brand {
    position: absolute; left: 0; top: 120px; width: 100%;
    display: flex; justify-content: center; align-items: center; gap: 16px;
  }
  .brand-square { width: 30px; height: 30px; background: var(--brand); }
  .front-brand .brand-name {
    color: var(--white); font-weight: 600; font-size: 46px;
    letter-spacing: -0.5px; line-height: 1;
  }
  .web-tab {
    position: absolute; left: 164px; top: 269px; width: 252px; height: 43px;
    background: linear-gradient(90deg, var(--cyan) 20%, var(--blue) 80%);
    clip-path: polygon(14px 0, calc(100% - 14px) 0, 100% 50%, calc(100% - 14px) 100%, 14px 100%, 0 50%);
    display: flex; align-items: center; justify-content: center;
    color: var(--navy); font-size: 16.5px; font-weight: 500;
  }

  /* Back */
  .card-back { top: 624px; width: 577px; height: 356px; }
  .back-panel {
    position: absolute; left: 0; top: 0; width: 230px; height: 100%;
    background: var(--navy);
  }
  .back-brand {
    position: absolute; left: 0; top: 88px; width: 230px;
    display: flex; justify-content: center; align-items: center; gap: 10px;
  }
  .back-brand .brand-square { width: 22px; height: 22px; }
  .back-brand .brand-name {
    color: var(--brand); font-weight: 600; font-size: 30px; line-height: 1;
  }
  .holder { position: absolute; left: 270px; top: 50px; }
  .holder-name {
    color: var(--navy); font-weight: 600; font-size: 24px; line-height: 1.1;
  }
  .holder-title {
    color: var(--navy); font-weight: 400; font-size: 17px; line-height: 1.1;
  }
  .divider {
    position: absolute; left: 273px; top: 114px; width: 208px; height: 1.5px;
    background: linear-gradient(90deg, var(--cyan) 0 50%, var(--blue) 50% 100%);
  }
  .icon-strip {
    position: absolute; left: 206px; top: 178px; width: 48px; height: 127px;
    background: linear-gradient(0deg, var(--cyan) 0%, var(--blue) 100%);
    clip-path: polygon(50% 0, 100% 13px, 100% calc(100% - 13px), 50% 100%, 0 calc(100% - 13px), 0 13px);
  }
  .icon {
    position: absolute; left: 11px; width: 26px; height: 26px; border-radius: 50%;
    background: var(--navy); display: flex; align-items: center; justify-content: center;
  }
  .icon svg { width: 15px; height: 15px; }
  .contact-list { position: absolute; left: 273px; top: 197px; list-style: none; }
  .contact-list li {
    color: var(--ink); font-size: 17.5px; line-height: 30.5px; height: 30.5px;
  }
</style>
</head>
<body>
<div class="canvas">

  <section class="card card-front">
    <div class="front-band"></div>
    <div class="front-brand">
      <span class="brand-square"></span>
      <span class="brand-name">VERODEX</span>
    </div>
    <div class="web-tab">www.verodexmarket.com</div>
  </section>

  <section class="card card-back">
    <div class="back-panel"></div>
    <div class="back-brand">
      <span class="brand-square"></span>
      <span class="brand-name">VERODEX</span>
    </div>

    <div class="holder">
      <p class="holder-name">DANIEL HARTLEY</p>
      <p class="holder-title">Managing Director</p>
    </div>
    <div class="divider"></div>

    <div class="icon-strip">
      <span class="icon" style="top:21px">
        <svg viewBox="0 0 24 24" fill="none" stroke="#fff" stroke-width="2" stroke-linecap="round" stroke-linejoin="round"><path d="M22 16.9v3a2 2 0 0 1-2.2 2 19.8 19.8 0 0 1-8.6-3.1 19.5 19.5 0 0 1-6-6A19.8 19.8 0 0 1 2.1 4.2 2 2 0 0 1 4.1 2h3a2 2 0 0 1 2 1.7c.1 1 .4 1.9.7 2.8a2 2 0 0 1-.5 2.1L8 9.8a16 16 0 0 0 6 6l1.3-1.3a2 2 0 0 1 2.1-.4c.9.3 1.8.6 2.8.7a2 2 0 0 1 1.7 2z"/></svg>
      </span>
      <span class="icon" style="top:52px">
        <svg viewBox="0 0 24 24" fill="none" stroke="#fff" stroke-width="2" stroke-linejoin="round"><rect x="2" y="5" width="20" height="14"/><path d="M2 5l10 8 10-8M2 19l7-7M22 19l-7-7"/></svg>
      </span>
      <span class="icon" style="top:82px">
        <svg viewBox="0 0 24 24" fill="none" stroke="#fff" stroke-width="1.8"><circle cx="12" cy="12" r="9.5"/><ellipse cx="12" cy="12" rx="4.5" ry="9.5"/><path d="M2.5 12h19M4 7h16M4 17h16M12 2.5v19"/></svg>
      </span>
    </div>

    <ul class="contact-list">
      <li>044-987 650 321</li>
      <li>hello@verodex.com</li>
      <li>www.verodexmarket.com</li>
    </ul>
  </section>

</div>
</body>
</html>
```